Custom Cabinet Shop Needs a website design

Hi,
We need a website for a Custom Cabinet Shop and Cabinet parts manufacturing business.
The business has two sides to it. One side provides custom Kitchens, vanities, entertainment units, offices and what not to homeowners and contractors.
The 2nd side of the business provides built to order cabinet boxes and other parts required to put together a project to other cabinet shops, small contractors looking to install there own cabinets.
Website will need a Gallery to display work.
Color scheme to go well with logo.
current website is www.brambleoakcustomcabinets.com
being changed to www.brambleoak.ca
Logo Included in attached files.
Tagline "Joinery with Spirit"
Mission Statement "Our passion is to deliver inspired cabinetry solutions to suit all your needs, supported by our phenomenal star class customer service"
The website should convey quality and professionalism.
Thank you.
Homeowners/ Contractors
Entertainment

```html
<!DOCTYPE html>
<html lang="en">
<head>
<meta charset="utf-8">
<title>Brambleoak Custom Cabinets</title>
<link href="https://fonts.googleapis.com/css2?family=Oswald:wght@400;500&family=Open+Sans:wght@400;600&display=swap" rel="stylesheet">
<style>
:root{
  --orange:#e8431d;
  --dark:#2b2b2b;
  --nav:#3a3a3a;
  --text:#555;
  --muted:#888;
  --light:#ececec;
  --white:#fff;
}
*{box-sizing:border-box;margin:0;padding:0}
html,body{width:826px;height:1200px;overflow:hidden;background:var(--white);font-family:"Open Sans",Arial,sans-serif;color:var(--text)}
.page{position:relative;width:826px;height:1200px}
.wrap{width:750px;margin:0 auto;position:relative}

.topbar{height:47px}
.topbar .wrap{height:47px;display:flex;align-items:center;justify-content:space-between}
.brand{display:flex;align-items:center;gap:8px}
.brand-mark{width:26px;height:26px;border-radius:50%;background:var(--orange)}
.brand-name{font-family:"Oswald",sans-serif;font-weight:500;font-size:21px;letter-spacing:1px;color:var(--dark)}
.search{display:flex;width:150px;height:20px;border:1px solid #ccc}
.search span{flex:1;font-size:9px;color:var(--muted);padding:4px 6px}
.search i{width:22px;background:var(--dark);display:flex;align-items:center;justify-content:center}

.mainnav{height:27px;background:var(--nav)}
.mainnav ul{list-style:none;display:flex;height:27px}
.mainnav li{font-family:"Oswald",sans-serif;font-size:10px;color:#ddd;letter-spacing:.5px;padding:0 20px;line-height:27px}
.mainnav li.active{background:var(--orange);color:var(--white)}

.hero{position:relative;height:366px;background:linear-gradient(160deg,#d9d6d0 0%,#b8b0a4 35%,#6f655b 70%,#2f2a26 100%)}
.hero-caption{position:absolute;left:55px;top:154px}
.hero-title{display:inline-block;background:var(--orange);color:var(--white);font-family:"Oswald",sans-serif;font-size:21px;padding:2px 12px}
.hero-text{width:370px;background:rgba(30,30,30,.75);color:#eee;font-size:10px;line-height:1.6;padding:10px 12px}
.hero-arrow{position:absolute;top:170px;width:18px;height:26px;background:rgba(0,0,0,.35)}

.welcome{text-align:center;padding:24px 0 0;height:206px}
h2{font-family:"Oswald",sans-serif;font-weight:400;font-size:25px;color:var(--dark)}
.mission{color:var(--orange);font-weight:600;font-size:10px;line-height:1.55;width:560px;margin:8px auto 8px}
.intro{font-size:8.5px;line-height:1.6;width:640px;margin:0 auto}
.btn{display:inline-block;margin-top:14px;background:var(--orange);color:var(--white);font-family:"Oswald",sans-serif;font-size:10px;padding:5px 14px}

.work{background:var(--light);height:236px;padding-top:26px;text-align:center}
.work .intro{margin-top:8px;width:560px}
.thumbs{display:flex;gap:10px;justify-content:center;margin-top:22px;position:relative}
.thumb{width:138px;height:90px}
.t1{background:linear-gradient(135deg,#8a6a56,#3a2c25)}
.t2{background:linear-gradient(135deg,#a08b74,#4b3c30)}
.t3{background:linear-gradient(135deg,#6c5a4c,#2a221d)}
.t4{background:linear-gradient(135deg,#c4b8a8,#7a6a58)}
.t5{background:linear-gradient(135deg,#9a8a78,#3f352c)}
.side-arrow{position:absolute;top:36px}

.testimonials{text-align:center;padding-top:38px;height:233px}
.quotes{display:flex;gap:22px;justify-content:center;margin-top:16px}
.quote{width:220px;text-align:left}
.quote p{border:1px solid #ddd;font-size:8.5px;line-height:1.6;padding:8px 10px}
.author{display:flex;align-items:center;gap:12px;margin-top:10px;padding-left:12px}
.avatar{width:30px;height:30px;border-radius:50%;background:linear-gradient(#d9c7b8,#a88f7c)}
.author span{color:var(--orange);font-size:9px}

.footer{position:absolute;left:0;right:0;bottom:0;height:85px;background:var(--dark);color:#ccc}
.footer .wrap{display:flex;justify-content:space-between;padding-top:20px}
.flinks{display:flex;font-size:8.5px}
.flinks span{padding:0 8px;border-left:1px solid #666}
.flinks span:first-child{padding-left:0;border:0}
.copy{font-size:8px;color:#999;margin-top:14px}
.follow{font-size:8.5px}
.socials{display:flex;gap:6px;margin-top:8px}
.socials i{width:16px;height:16px;border-radius:50%;background:#777}
</style>
</head>
<body>
<div class="page">
  <header class="topbar">
    <div class="wrap">
      <div class="brand"><span class="brand-mark"></span><span class="brand-name">BRAMBLEOAK</span></div>
      <div class="search"><span>Search</span><i><svg width="10" height="10" viewBox="0 0 10 10"><circle cx="4" cy="4" r="3" fill="none" stroke="#fff" stroke-width="1.3"/><line x1="6.2" y1="6.2" x2="9" y2="9" stroke="#fff" stroke-width="1.3"/></svg></i></div>
    </div>
  </header>
  <nav class="mainnav">
    <div class="wrap">
      <ul><li class="active">HOME</li><li>ABOUT US</li><li>GALLERY</li><li>SERVICES</li><li>WARRANTY</li><li>CONTACT US</li></ul>
    </div>
  </nav>
  <section class="hero" role="img" aria-label="Photograph of a finished white kitchen with custom cabinets and a granite island">
    <div class="hero-caption">
      <div class="hero-title">Joinery with Spirit</div>
      <div class="hero-text">Crafted cabinetry built to last, finished by hand in our own shop for homeowners and contractors across the region.</div>
    </div>
  </section>
  <section class="welcome">
    <h2>Welcome to Our Site</h2>
    <p class="mission">Our passion is to deliver inspired cabinetry solutions to suit all your needs, supported by our phenomenal star class customer service.</p>
    <p class="intro">Every project starts with a conversation about how you live and work. From kitchens and vanities to entertainment units and home offices, our team designs, builds and installs cabinetry that fits your space and your budget. We also supply built-to-order cabinet boxes and parts to shops and contractors who install their own work, with dependable lead times and clean, square assembly.</p>
    <span class="btn">READ MORE</span>
  </section>
  <section class="work">
    <h2>Work Done</h2>
    <p class="intro">Browse a selection of recent kitchens, vanities and built-ins completed for local homeowners. Each piece is measured, built and finished in our shop, then installed with care by our own crew.</p>
    <div class="thumbs">
      <svg class="side-arrow" style="left:22px" width="10" height="16" viewBox="0 0 10 16"><polyline points="8,2 2,8 8,14" fill="none" stroke="#999" stroke-width="2"/></svg>
      <div class="thumb t1" role="img" aria-label="Kitchen project photo"></div>
      <div class="thumb t2" role="img" aria-label="Kitchen project photo"></div>
      <div class="thumb t3" role="img" aria-label="Dining and kitchen project photo"></div>
      <div class="thumb t4" role="img" aria-label="Open kitchen project photo"></div>
      <div class="thumb t5" role="img" aria-label="Cabinet project photo"></div>
      <svg class="side-arrow" style="right:22px" width="10" height="16" viewBox="0 0 10 16"><polyline points="2,2 8,8 2,14" fill="none" stroke="#999" stroke-width="2"/></svg>
    </div>
  </section>
  <section class="testimonials">
    <h2>Testimonials</h2>
    <div class="quotes">
      <div class="quote"><p>The new kitchen came in on time and looks better than we imagined. Friendly crew, tidy work and great advice throughout.</p><div class="author"><span class="avatar" role="img" aria-label="Customer portrait"></span><span>Dana Fields</span></div></div>
      <div class="quote"><p>Our vanities were built exactly to size and installed in a day. Quality finish and honest pricing from start to finish.</p><div class="author"><span class="avatar" role="img" aria-label="Customer portrait"></span><span>Dana Fields</span></div></div>
      <div class="quote"><p>We order cabinet boxes for our own jobs every month. Always square, always on schedule, and easy to work with.</p><div class="author"><span class="avatar" role="img" aria-label="Customer portrait"></span><span>Dana Fields</span></div></div>
    </div>
  </section>
  <footer class="footer">
    <div class="wrap">
      <div>
        <div class="flinks"><span>Home</span><span>About Us</span><span>Gallery</span><span>Services</span><span>Contact Us</span></div>
        <div class="copy">Copyright © 2015 Brambleoak. All rights reserved.</div>
      </div>
      <div class="follow">Follow Us
        <div class="socials"><i></i><i></i><i></i><i></i><i></i></div>
      </div>
    </div>
  </footer>
</div>
</body>
</html>
```